DJ Colm Vetter

I'm looking for a professional but still artsy/progressive design. I come from a hip hop/club DJ background playing a lot of underground music but have switched to doing more corporate parties and weddings recently. I am all about keeping the dancefloor moving and emotionally connecting with the crowd. I'd like a trendy/updated color palette. Something that's clean enough that looks professional but also trendy enough to convey that by the end of the night we'll be sweatily dancing to the latest hits. Some designers/artists I like: Tarn Olquist, Pavel Remy, Wendell Quarrie, Lumeno 7400, Silas Dravin.

```html
<!DOCTYPE html>
<html lang="en">
<head>
<meta charset="utf-8">
<title>DJ Colm Vetter — Business Card</title>
<link rel="stylesheet" href="https://fonts.googleapis.com/css2?family=Oswald:wght@500;700&family=Open+Sans:wght@400;600&display=swap">
<style>
  :root {
    --stage: #2f2f2f;
    --orange: #e8771d;
    --orange-soft: #ef8a36;
    --ink: #111111;
    --text: #444444;
    --paper: #ffffff;
  }
  * { box-sizing: border-box; margin: 0; padding: 0; }
  html, body {
    width: 1200px; height: 866px; overflow: hidden;
    background: var(--stage);
  }
  .canvas { position: relative; width: 1200px; height: 866px; }

  .card {
    position: absolute;
    width: 620px; height: 354px;
    box-shadow: 0 6px 18px rgba(0,0,0,.45);
    overflow: hidden;
  }

  /* Front */
  .card--front {
    left: 70px; top: 70px;
    background: linear-gradient(160deg, #f1f1f1 0%, var(--paper) 35%);
    border-bottom: 10px solid var(--orange);
  }
  .contact { position: absolute; left: 40px; top: 58px; }
  .contact__name {
    font-family: "Oswald", sans-serif; font-weight: 700;
    font-size: 26px; color: var(--orange); text-transform: uppercase;
    letter-spacing: .5px; line-height: 1.1;
  }
  .contact__role {
    font-family: "Open Sans", sans-serif; font-size: 15px;
    color: var(--text); margin-bottom: 12px;
  }
  .contact__list { list-style: none; }
  .contact__item {
    display: flex; align-items: center; gap: 8px;
    font-family: "Open Sans", sans-serif; font-size: 15px;
    color: var(--text); line-height: 23px;
  }
  .contact__icon { width: 12px; height: 12px; fill: var(--orange); flex: none; }

  .brand {
    position: absolute; right: 44px; top: 128px;
    font-family: "Oswald", sans-serif; font-weight: 700;
    font-size: 44px; color: var(--ink); text-transform: uppercase;
    letter-spacing: 1px; line-height: 1;
  }
  .address {
    position: absolute; right: 44px; bottom: 26px; text-align: right;
    font-family: "Open Sans", sans-serif; font-size: 15px;
    color: var(--text); line-height: 21px;
  }

  /* Back */
  .card--back {
    left: 510px; top: 442px;
    background: radial-gradient(circle at 40% 55%, var(--orange-soft) 0%, var(--orange) 60%);
    display: flex; align-items: center; justify-content: center;
  }
  .brand--reverse {
    position: static;
    color: var(--paper); font-size: 52px;
  }
</style>
</head>
<body>
<main class="canvas">

  <section class="card card--front" aria-label="Business card front">
    <div class="contact">
      <h1 class="contact__name">Rowan Ashby</h1>
      <p class="contact__role">Managing Director</p>
      <ul class="contact__list">
        <li class="contact__item">
          <svg class="contact__icon" viewBox="0 0 12 12" aria-hidden="true"><path d="M1 3c0-1 1-2 2-2h6c1 0 2 1 2 2v1H8V3H4v1H1z M2 5h8l1 6H1z"/></svg>
          044-870 315 264
        </li>
        <li class="contact__item">
          <svg class="contact__icon" viewBox="0 0 12 12" aria-hidden="true"><path d="M3 0h6v12H3z M4 1.5v8h4v-8z"/></svg>
          044-870 315 265
        </li>
        <li class="contact__item">
          <svg class="contact__icon" viewBox="0 0 12 12" aria-hidden="true"><path d="M0 2h12v8H0z M1 3l5 4 5-4" stroke="#fff" stroke-width="1"/></svg>
          info@colmvetter.fm
        </li>
        <li class="contact__item">
          <svg class="contact__icon" viewBox="0 0 12 12" aria-hidden="true"><circle cx="6" cy="6" r="6"/><path d="M0 6h12M6 0c-3 3-3 9 0 12M6 0c3 3 3 9 0 12" stroke="#fff" stroke-width=".8" fill="none"/></svg>
          www.colmvetter.fm
        </li>
      </ul>
    </div>

    <p class="brand">DJ Colm Vetter</p>

    <address class="address">
      48 Harbor Lane,<br>Portvale, 204817
    </address>
  </section>

  <section class="card card--back" aria-label="Business card back">
    <p class="brand brand--reverse">DJ Colm Vetter</p>
  </section>

</main>
</body>
</html>
```